Health and Wellness company needs flyer to promote free seminar

Corvella Motion studio is a health and wellness company that offers an exercise program designed by physical therapists to help relieve pain and improve mobility. Our business is a new concept that is not well understood by the public. In order to promote our business we offer a free seminar where we present information regarding the underlying cause of pain and tightness. During the seminar we also perform a posture screen and movement testing for all participants.

Target Market(s)

Mostly healthy and active women ages 25-65

Industry/Entity Type

Health And Wellness

Font styles to use
Sans Serif

Colors

Designer to choose colors to be used in the design.

Requirements
Must have
• Title: Eliminate Pain and Tightness For Good
• Paragraph: Corvella Motion Studio offers a free 60 minute seminar: "The Busy Walker's Manual for Stretching and Living Lighter."
• What to Expect:
• • Identify the underlying cause of your pain and mobility issues
• • Expose what gets in the way of you moving and feeling better
• • Learn why traditional exercises don’t help and can actually make the problem worse
• • Reveal what your posture is saying and how that impacts you
• • Experience your muscle imbalances through movement tests
• • Discover the training method that realigns your posture, increases your mobility and reduces your pain
• Call to action: RSVP online at corvellamotionstudio.com
Nice to have
• Use a relevant image showing a female dealing with tightness in the low back, legs, etc.
• Emphasize that the seminar is FREE.
• Make the call to action prominent.

```html
<!DOCTYPE html>
<html lang="en">
<head>
<meta charset="utf-8">
<title>Corvella Motion Studio – Free Seminar Flyer</title>
<link href="https://fonts.googleapis.com/css2?family=Questrial&family=Lato:wght@400;700&display=swap" rel="stylesheet">
<style>
  :root {
    --orange: #f39020;
    --purple: #5753a6;
    --purple-dark: #3e4282;
    --purple-mid: #5458a0;
    --ink: #2b2b2b;
    --white: #ffffff;
    --stage: #e4e4e4;
    --photo-light: #eef4f8;
    --photo-mid: #d5e3ec;
  }
  * { margin: 0; padding: 0; box-sizing: border-box; }
  html, body { width: 1200px; height: 1200px; overflow: hidden; background: var(--stage); }
  .flyer {
    position: absolute; left: 200px; top: 38px;
    width: 800px; height: 1123px;
    background: var(--white);
    box-shadow: 0 4px 18px rgba(0,0,0,.18);
    overflow: hidden;
  }
  .title-column {
    position: absolute; left: 0; top: 0;
    width: 205px; height: 987px;
    background: var(--orange);
  }
  .bracket { position: absolute; left: 27px; width: 146px; height: 30px; }
  .bracket--top { top: 38px; }
  .bracket--bottom { top: 920px; }
  .headline {
    position: absolute; left: 30px; top: 70px;
    height: 848px; width: 150px;
    writing-mode: vertical-rl;
    transform: rotate(180deg);
    text-align: center;
    white-space: nowrap;
    font-family: "Questrial", sans-serif;
    font-weight: 400;
    color: var(--white);
    line-height: 1.1;
  }
  .headline__main { display: block; font-size: 55px; }
  .headline__accent { display: block; font-size: 52px; letter-spacing: 1px; }

  .brand {
    position: absolute; right: 32px; top: 24px;
    display: flex; align-items: center; gap: 12px;
  }
  .brand__mark { width: 30px; height: 30px; background: var(--orange); }
  .brand__name {
    font-family: "Questrial", sans-serif; font-size: 27px;
    color: var(--purple);
  }

  .hero-photo {
    position: absolute; left: 205px; top: 103px;
    width: 595px; height: 473px;
    background:
      linear-gradient(to bottom, rgba(255,255,255,0) 60%, var(--white) 100%),
      linear-gradient(120deg, var(--photo-light) 0%, var(--photo-mid) 55%, var(--photo-light) 100%);
  }

  .content { position: absolute; left: 225px; top: 510px; width: 540px; }
  .intro {
    font-family: "Questrial", sans-serif; font-size: 23px; line-height: 28px; color: var(--ink);
  }
  .offer {
    font-family: "Questrial", sans-serif; font-size: 37px; line-height: 44px; font-weight: 700;
    color: var(--purple); margin-top: 4px; -webkit-text-stroke: .6px var(--purple);
  }
  .offer span { color: var(--ink); -webkit-text-stroke: .6px var(--ink); }
  .seminar-title {
    font-family: "Questrial", sans-serif; font-size: 28px;
    color: var(--orange); line-height: 35px; margin-top: 6px;
    -webkit-text-stroke: .5px var(--orange);
  }
  .expect-heading {
    font-family: "Lato", sans-serif; font-weight: 700; font-size: 21px; line-height: 25px;
    color: var(--ink); text-decoration: underline; margin: 12px 0 10px 4px;
  }
  .expect-list { list-style: none; }
  .expect-list li {
    position: relative; padding-left: 26px;
    font-family: "Lato", sans-serif; font-size: 17.5px; line-height: 22px;
    color: var(--ink); margin-bottom: 10px;
  }
  .expect-list svg { position: absolute; left: 2px; top: 3px; width: 18px; height: 16px; }

  .cta {
    position: absolute; left: 0; top: 987px; width: 800px; height: 136px;
    background: linear-gradient(90deg, var(--purple-dark) 0%, var(--purple-mid) 50%, var(--purple-dark) 100%);
    text-align: center; color: var(--white); font-family: "Lato", sans-serif;
    padding-top: 26px;
  }
  .cta__lead { font-size: 24px; }
  .cta__url { font-size: 29px; font-weight: 700; margin-top: 8px; }
</style>
</head>
<body>
  <main class="flyer">
    <aside class="title-column">
      <svg class="bracket bracket--top" viewBox="0 0 146 30">
        <path d="M3 30 V3 H143 V30" fill="none" stroke="#fff" stroke-width="6"/>
      </svg>
      <h1 class="headline">
        <span class="headline__main">Eliminate Pain and Tightness</span>
        <span class="headline__accent">FOR GOOD</span>
      </h1>
      <svg class="bracket bracket--bottom" viewBox="0 0 146 30">
        <path d="M3 0 V27 H143 V0" fill="none" stroke="#fff" stroke-width="6"/>
      </svg>
    </aside>

    <header class="brand">
      <span class="brand__mark"></span>
      <span class="brand__name">Corvella Motion Studio</span>
    </header>

    <div class="hero-photo" role="img" aria-label="Photo of a woman sitting on a bed in a bright bedroom, holding her lower back in discomfort"></div>

    <section class="content">
      <p class="intro">Corvella Motion Studio offers a</p>
      <h2 class="offer">Free 60 minute seminar<span>:</span></h2>
      <p class="seminar-title">"The Busy Walker's Manual for Stretching and Living Lighter."</p>
      <h3 class="expect-heading">What to Expect:</h3>
      <ul class="expect-list">
        <li><svg viewBox="0 0 18 16"><rect x="1" y="3" width="12" height="12" fill="none" stroke="#5753a6" stroke-width="1.6"/><path d="M4 9 L7 12 L17 1" fill="none" stroke="#5753a6" stroke-width="2.2"/></svg>Identify the underlying cause of your pain and mobility issues</li>
        <li><svg viewBox="0 0 18 16"><rect x="1" y="3" width="12" height="12" fill="none" stroke="#5753a6" stroke-width="1.6"/><path d="M4 9 L7 12 L17 1" fill="none" stroke="#5753a6" stroke-width="2.2"/></svg>Expose what gets in the way of you moving and feeling better</li>
        <li><svg viewBox="0 0 18 16"><rect x="1" y="3" width="12" height="12" fill="none" stroke="#5753a6" stroke-width="1.6"/><path d="M4 9 L7 12 L17 1" fill="none" stroke="#5753a6" stroke-width="2.2"/></svg>Learn why traditional exercises don’t help and can actually make the problem worse</li>
        <li><svg viewBox="0 0 18 16"><rect x="1" y="3" width="12" height="12" fill="none" stroke="#5753a6" stroke-width="1.6"/><path d="M4 9 L7 12 L17 1" fill="none" stroke="#5753a6" stroke-width="2.2"/></svg>Reveal what your posture is saying and how that impacts you</li>
        <li><svg viewBox="0 0 18 16"><rect x="1" y="3" width="12" height="12" fill="none" stroke="#5753a6" stroke-width="1.6"/><path d="M4 9 L7 12 L17 1" fill="none" stroke="#5753a6" stroke-width="2.2"/></svg>Experience your muscle imbalances through movement tests</li>
        <li><svg viewBox="0 0 18 16"><rect x="1" y="3" width="12" height="12" fill="none" stroke="#5753a6" stroke-width="1.6"/><path d="M4 9 L7 12 L17 1" fill="none" stroke="#5753a6" stroke-width="2.2"/></svg>Discover the training method that realigns your posture, increases your mobility and reduces your pain</li>
      </ul>
    </section>

    <footer class="cta">
      <p class="cta__lead">Sign up online at</p>
      <p class="cta__url">www.corvellamotionstudio.com/free-seminar</p>
    </footer>
  </main>
</body>
</html>
```